Construction Company

Design a clutter free business card, it can be double-sided utilizing the logo for VKM Ltd simple with all relevant contact information.

Please also a letterhead design to function for the purposes of invoicing, all mail requirements, with header to be distinctive while the footer ties page together and incorporates all necessary information.

For now, please use generic / dummy text and when a winner is selected, I will disclose the contact information.

Hi Designers! Please read the updated brief which includes the design of a business card and letterhead. Thank you!

```html
<!DOCTYPE html>
<html lang="en">
<head>
<meta charset="utf-8">
<title>VKM Ltd – Business Card</title>
<link rel="stylesheet" href="https://fonts.googleapis.com/css2?family=Playfair+Display:wght@700&family=Tinos:wght@700&family=Arimo:wght@400&display=swap">
<style>
  :root {
    --backdrop: #c4c4c4;
    --brand-blue: #00308f;
    --brand-gold: #b8962a;
    --paper: #ffffff;
    --ink: #333333;
    --rule: #9a9a9a;
  }
  * { margin: 0; padding: 0; box-sizing: border-box; }
  html, body { width: 1200px; height: 1200px; overflow: hidden; }
  body { background: var(--backdrop); position: relative; font-family: "Arimo", Arial, sans-serif; }

  .card { position: absolute; top: 303px; width: 368px; height: 594px; }
  .card--front { left: 200px; background: var(--brand-blue); }
  .card--back { left: 599px; width: 364px; background: var(--paper); text-align: center; }

  .wordmark {
    position: absolute; display: flex; align-items: center; gap: 10px;
    font-family: "Playfair Display", Georgia, serif; font-weight: 700;
    font-size: 58px; letter-spacing: 1px; line-height: 1; white-space: nowrap;
  }
  .wordmark__dot { width: 18px; height: 18px; border-radius: 50%; background: var(--brand-gold); flex: none; }
  .card--front .wordmark { left: 44px; top: 480px; color: var(--paper); }
  .card--back .wordmark { left: 50%; transform: translateX(-50%); top: 120px; color: var(--brand-blue); }

  .holder { position: absolute; top: 308px; left: 0; width: 100%; }
  .holder__name {
    font-family: "Tinos", "Times New Roman", serif; font-weight: 700;
    font-size: 21px; color: var(--brand-blue); letter-spacing: 0.5px; line-height: 24px;
  }
  .holder__role { font-size: 17px; color: var(--ink); line-height: 20px; }

  .contact-icons { position: absolute; top: 364px; left: 0; width: 100%; display: flex; justify-content: center; align-items: center; gap: 4px; }
  .contact-icons__line { width: 36px; height: 1px; background: var(--rule); margin: 0 4px; }
  .contact-icons__tile { width: 25px; height: 25px; border-radius: 3px; background: var(--brand-blue); display: flex; align-items: center; justify-content: center; }

  .contact-list { position: absolute; top: 400px; left: 0; width: 100%; font-size: 17px; line-height: 21.5px; color: var(--ink); list-style: none; }
  .contact-list__accent { color: var(--brand-blue); }

  .contact-rule { position: absolute; top: 497px; left: 88px; width: 195px; height: 1px; background: var(--rule); }

  .address { position: absolute; top: 509px; left: 0; width: 100%; font-size: 17px; line-height: 22px; color: var(--ink); font-style: normal; }
</style>
</head>
<body>

<section class="card card--front" aria-label="Business card front">
  <div class="wordmark"><span class="wordmark__dot"></span>VKM LTD</div>
</section>

<section class="card card--back" aria-label="Business card back">
  <div class="wordmark"><span class="wordmark__dot"></span>VKM LTD</div>

  <div class="holder">
    <p class="holder__name">DANIEL HARPER</p>
    <p class="holder__role">Managing Director</p>
  </div>

  <div class="contact-icons">
    <span class="contact-icons__line"></span>
    <span class="contact-icons__tile">
      <svg width="15" height="15" viewBox="0 0 16 16" fill="#fff"><path d="M2 6c0-2 3-3 6-3s6 1 6 3v1h-3V5.6C10 5.2 9 5 8 5s-2 .2-3 .6V7H2z"/><rect x="4" y="8" width="8" height="6" rx="1"/></svg>
    </span>
    <span class="contact-icons__tile">
      <svg width="15" height="15" viewBox="0 0 16 16" fill="none" stroke="#fff" stroke-width="1.6"><rect x="4.5" y="1.5" width="7" height="13" rx="1"/><circle cx="8" cy="12" r="0.6" fill="#fff"/></svg>
    </span>
    <span class="contact-icons__tile">
      <svg width="15" height="15" viewBox="0 0 16 16" fill="none" stroke="#fff" stroke-width="1.4"><rect x="1.5" y="3.5" width="13" height="9"/><path d="M1.5 3.5l6.5 5 6.5-5M1.5 12.5l5-4M14.5 12.5l-5-4"/></svg>
    </span>
    <span class="contact-icons__tile">
      <svg width="15" height="15" viewBox="0 0 16 16" fill="none" stroke="#fff" stroke-width="1.4"><circle cx="8" cy="8" r="6"/><path d="M2 8h12M8 2c2 2 2 10 0 12M8 2c-2 2-2 10 0 12"/></svg>
    </span>
    <span class="contact-icons__line"></span>
  </div>

  <ul class="contact-list">
    <li>021-555 014 672</li>
    <li>021-555 014 673</li>
    <li>info@example.com</li>
    <li>www.<span class="contact-list__accent">example</span>.com</li>
  </ul>

  <div class="contact-rule"></div>

  <address class="address">
    18, Harbour View Road<br>
    30418,Northland
  </address>
</section>

</body>
</html>
```